Healthcare/Medical Consultant Company

QRN is a Healthcare Conultant Company. We help doctors manage the business side of their medical practice.
We already have a very basic world press design. We want an upgraded design that conveys partnership, healthcare expertise and healthcare innovation to our client. It needs to have a sleek, clean, modern and inclusive look. Pictures need need to convey diversity (including pictures of people of all races and shows both men and women working together in a healthcare environment to make it better). The Pictures on the home page should particularly illustrate diversity and Healthcare expertise. The company logo is blue and white but the site doesn’t have to follow the exact same theme but the logo needs to blend well with the chosen theme. The logo should ideally be in the header of the website. We would also like the following included in our website:

1. Pages should include: a home page, About Us page, Services page, Get a quote page, Contact Us page, Staff page(where we can add pictures and bio for staff).

2. The Drop down menu for services should have hyperlinks ( for each service)Leading to a page that provides detailed info about that specific service. Our services include: Revenue Cycle Management, Regulatory Compliance, Human Resources Management, & practice Management.

3. Links to social media should in the header or footer of each page.

4. Contact info should be in the footer of each page.

5. Clients should be an email to us from the contact page.

Target Market(s)

Physician Medical Practices

Industry/Entity Type

Medical

Coding

Coded - Design and coding required

Font styles to use
Sans Serif

Colors

Designer to choose colors to be used in the design.

Requirements
Must have
• See project description
Nice to have
• See project description

```html
<!DOCTYPE html>
<html lang="en">
<head>
<meta charset="utf-8">
<title>QRN – Quarryline Health Partners</title>
<link href="https://fonts.googleapis.com/css2?family=Poppins:wght@400;500;600;700&display=swap" rel="stylesheet">
<style>
:root{
  --navy:#1c3f8c;
  --blue:#1f6fc4;
  --sky:#2b8fd6;
  --ink:#333;
  --muted:#555;
  --light:#f1f1f1;
  --dark:#2e2e2e;
  --white:#fff;
}
*{box-sizing:border-box;margin:0;padding:0}
html,body{width:1200px;height:3321px;overflow:hidden}
body{position:relative;font-family:'Poppins',sans-serif;color:var(--ink);background:var(--white)}
.abs{position:absolute}

/* header */
.site-header{left:0;top:0;width:1200px;height:166px;background:var(--white)}
.brand{left:100px;top:26px;width:345px;text-align:center;color:var(--navy);font-weight:600}
.brand-mark{font-size:64px;line-height:70px;letter-spacing:4px}
.brand-name{font-size:17px;line-height:24px}
.quote-btn{left:956px;top:33px;width:142px;height:51px;border-radius:26px;background:linear-gradient(180deg,var(--blue),var(--navy));color:var(--white);font-size:19px;line-height:51px;text-align:center}
.main-nav{top:110px;font-size:16px;font-weight:500;color:#111;letter-spacing:.2px}

/* hero */
.hero{left:0;top:166px;width:1200px;height:675px;background:linear-gradient(135deg,#5b6a74 0%,#8e9aa1 45%,#6a7780 100%)}
.hero-shade{left:0;top:166px;width:1200px;height:675px;background:rgba(20,30,40,.35)}
.hero-title{left:0;top:420px;width:1200px;text-align:center;color:var(--white);font-size:43px;line-height:60px;font-weight:500;letter-spacing:.5px}
.social-side{left:66px;width:18px;height:18px;border-radius:50%;border:2px solid var(--white)}
.follow{left:62px;color:var(--white);font-size:14px;transform:rotate(-90deg);transform-origin:left top;white-space:nowrap}
.dot{top:754px;width:23px;height:23px;border-radius:50%;border:2px solid var(--white)}
.dot.active{background:var(--white)}

/* services */
.section-title{left:0;width:1200px;text-align:center;font-weight:600}
.services-title{top:902px;font-size:36px;color:var(--sky)}
.service-card{top:1007px;width:295px;height:233px;background:var(--white);border:1px solid #ddd;box-shadow:0 3px 8px rgba(0,0,0,.18);padding:14px 22px 0;overflow:hidden}
.service-card.featured{background:linear-gradient(180deg,var(--sky),var(--navy));color:var(--white);border:none}
.service-card svg{display:block;height:56px}
.service-card h3{font-size:17px;font-weight:500;color:var(--navy);line-height:23px;margin:14px 0 7px}
.service-card.featured h3{color:var(--white)}
.service-card p{font-size:13px;line-height:23px;color:var(--muted);white-space:nowrap}
.service-card.featured p{color:var(--white)}
.details-tab{width:126px;height:32px;background:var(--navy);color:var(--white);font-size:14px;font-weight:600;line-height:32px;text-align:center;clip-path:polygon(10% 0,100% 0,90% 100%,0 100%)}

/* about */
.about{left:0;top:1320px;width:1200px;height:476px;background:linear-gradient(90deg,#242424,#3a3d40)}
.about-title{left:100px;top:1405px;font-size:36px;color:var(--white);font-weight:600}
.about-text{left:100px;top:1474px;width:520px;color:#eee;font-size:14px;line-height:30px}
.read-more{left:100px;top:1650px;width:132px;height:42px;border-radius:21px;background:var(--blue);color:var(--white);font-size:16px;font-weight:600;line-height:42px;text-align:center}
.about-frame{left:877px;top:1393px;width:237px;height:327px;background:var(--blue)}
.about-photo{left:629px;top:1408px;width:469px;height:297px;background:linear-gradient(135deg,#7d93a8,#c9d3da 50%,#51667b)}

/* contact */
.contact{left:0;top:1796px;width:1200px;height:642px;background:var(--light)}
.contact-title{top:1890px;font-size:36px;color:var(--navy)}
.field{background:var(--white);border:1px solid #ddd;box-shadow:0 2px 4px rgba(0,0,0,.12);font-size:15px;color:#444;padding:0 26px;line-height:58px}
.submit{left:516px;top:2265px;width:166px;height:62px;border-radius:31px;background:linear-gradient(180deg,var(--blue),var(--navy));color:var(--white);font-size:18px;font-weight:600;line-height:62px;text-align:center;box-shadow:0 3px 6px rgba(0,0,0,.3)}

/* testimonials */
.testimonials{left:0;top:2438px;width:1200px;height:472px;background:linear-gradient(90deg,#1d57a8,#3a79c4 60%,#2462b2)}
.testi-title{top:2505px;font-size:34px;color:var(--white)}
.testi-card{top:2633px;width:305px;height:197px;border:2px solid rgba(255,255,255,.85);text-align:center;color:var(--white);padding:62px 16px 0}
.testi-card p{font-size:13px;font-style:italic;line-height:24px}
.testi-card h4{font-size:19px;font-weight:500;margin-top:8px}
.avatar{top:2591px;width:84px;height:84px;border-radius:50%;border:3px solid var(--white);background:linear-gradient(180deg,#c8b7a3,#8b7866)}
.round-arrow{top:2706px;width:48px;height:48px;border-radius:50%;background:rgba(255,255,255,.35)}

/* footer */
.site-footer{left:0;top:2910px;width:1200px;height:411px;background:var(--dark)}
.foot-head{top:2995px;color:var(--white);font-size:21px;font-weight:600}
.foot-text{color:#ddd;font-size:13px;line-height:24px}
.foot-list{list-style:none;color:#ddd;font-size:13px;line-height:24px}
.foot-social{top:3169px;width:34px;height:34px;border-radius:50%;border:1.5px solid var(--white)}
.sub-input{left:824px;top:3074px;width:276px;height:36px;background:var(--white);font-size:12px;color:#777;line-height:36px;padding-left:14px}
.sub-btn{left:824px;top:3129px;width:108px;height:34px;border-radius:17px;background:var(--blue);color:var(--white);font-size:13px;font-weight:600;line-height:34px;text-align:center}
.foot-rule{left:91px;top:3237px;width:1009px;height:1px;background:#555}
.copyright{left:0;top:3262px;width:1200px;text-align:center;color:#ddd;font-size:13px}
</style>
</head>
<body>

<header class="site-header abs">
  <div class="brand abs"><div class="brand-mark">QRN</div><div class="brand-name">Quarryline Health Partners LLC</div></div>
  <div class="quote-btn abs">Get a quote</div>
  <nav>
    <span class="main-nav abs" style="left:635px">HOME</span>
    <span class="main-nav abs" style="left:711px">ABOUT US</span>
    <span class="main-nav abs" style="left:819px">SERVICES ▾</span>
    <span class="main-nav abs" style="left:937px">STAFF</span>
    <span class="main-nav abs" style="left:1012px">CONTACT US</span>
  </nav>
</header>

<section>
  <div class="hero abs" role="img" aria-label="Diverse team of doctors and nurses meeting around a table"></div>
  <div class="hero-shade abs"></div>
  <h1 class="hero-title abs">QUARRYLINE HEALTH PARTNERS<br>“ADVANCING HEALTHCARE”</h1>
  <span class="social-side abs" style="top:336px" aria-label="Social link"></span>
  <span class="social-side abs" style="top:378px" aria-label="Social link"></span>
  <span class="social-side abs" style="top:423px" aria-label="Social link"></span>
  <span class="social-side abs" style="top:465px" aria-label="Social link"></span>
  <span class="follow abs" style="top:620px">Follow us</span>
  <svg class="abs" style="left:0;top:700px" width="1200" height="141" viewBox="0 0 1200 141">
    <path d="M0,141 L0,30 Q600,150 1200,30 L1200,141 Z" fill="#fff"/>
    <path d="M0,38 Q600,170 1200,38" fill="none" stroke="#1f6fc4" stroke-width="9"/>
    <path d="M0,52 Q600,185 1200,52" fill="none" stroke="#1c3f8c" stroke-width="4"/>
  </svg>
  <span class="dot active abs" style="left:560px"></span>
  <span class="dot abs" style="left:591px"></span>
  <span class="dot abs" style="left:618px"></span>
</section>

<section>
  <h2 class="section-title services-title abs">OUR SERVICES</h2>
  <svg class="abs" style="left:46px;top:1094px" width="24" height="40"><path d="M20 4 L6 20 L20 36" fill="none" stroke="#777" stroke-width="4"/></svg>
  <svg class="abs" style="left:1128px;top:1094px" width="24" height="40"><path d="M4 4 L18 20 L4 36" fill="none" stroke="#777" stroke-width="4"/></svg>

  <article class="service-card abs" style="left:97px">
    <svg width="64" height="56" viewBox="0 0 64 64"><circle cx="16" cy="16" r="12" fill="none" stroke="#1f6fc4" stroke-width="3"/><rect x="8" y="44" width="10" height="16" fill="#1c3f8c"/><rect x="24" y="36" width="10" height="24" fill="#1c3f8c"/><rect x="40" y="28" width="10" height="32" fill="#1c3f8c"/><path d="M12 38 L36 18 L56 8" fill="none" stroke="#2b8fd6" stroke-width="3"/></svg>
    <h3>Revenue Cycle Management</h3>
    <p>In today’s increasingly complex health<br>care environment it’s important<br>now more than ever that medical</p>
  </article>
  <div class="details-tab abs" style="left:286px;top:1220px">View Details</div>

  <article class="service-card featured abs" style="left:443px">
    <svg width="90" height="56" viewBox="0 0 90 60"><rect x="3" y="3" width="84" height="48" fill="none" stroke="#fff" stroke-width="3"/><rect x="52" y="10" width="26" height="14" fill="none" stroke="#fff" stroke-width="2"/><line x1="12" y1="38" x2="78" y2="38" stroke="#fff" stroke-width="3"/><circle cx="30" cy="38" r="4" fill="#fff"/></svg>
    <h3>Regulatory &amp; Compliance<br>Management</h3>
    <p>In a heavily regulated healthcare<br>environment medical practices need<br>to be acutely aware of regulations</p>
  </article>

  <article class="service-card abs" style="left:784px">
    <svg width="64" height="56" viewBox="0 0 64 64"><circle cx="14" cy="14" r="9" fill="none" stroke="#1f6fc4" stroke-width="3"/><circle cx="38" cy="24" r="11" fill="none" stroke="#1c3f8c" stroke-width="3"/><path d="M18 60 Q38 34 58 60" fill="none" stroke="#1c3f8c" stroke-width="3"/></svg>
    <h3 style="font-size:20px;margin-bottom:4px">Practice Management</h3>
    <p>Practice Management is challenging<br>and it requires the right balance<br>of skill, knowledge, experience and<br>management expertise.</p>
  </article>
  <div class="details-tab abs" style="left:972px;top:1220px">View Details</div>
</section>

<section>
  <div class="about abs"></div>
  <h2 class="about-title abs">ABOUT US</h2>
  <p class="about-text abs">Quarryline Health Partners (QRN) is a healthcare consulting firm skilled at helping physician practices advance their strategic vision in an ever-evolving healthcare system. Quarryline Health Partners specializes in revenue cycle optimization, practice management improvement and developing new physician practices.</p>
  <div class="read-more abs">Read More</div>
  <div class="about-frame abs"></div>
  <div class="about-photo abs" role="img" aria-label="Diverse doctors and nurses walking together through a hospital corridor"></div>
</section>

<section>
  <div class="contact abs"></div>
  <h2 class="section-title contact-title abs">GET IN TOUCH</h2>
  <div class="field abs" style="left:239px;top:1962px;width:357px;height:59px">Name</div>
  <div class="field abs" style="left:604px;top:1962px;width:359px;height:59px">Phone Number</div>
  <div class="field abs" style="left:239px;top:2028px;width:357px;height:60px">Email</div>
  <div class="field abs" style="left:604px;top:2028px;width:359px;height:60px">Zipcode</div>
  <div class="field abs" style="left:239px;top:2099px;width:724px;height:151px;line-height:48px">Message</div>
  <div class="submit abs">SUBMIT</div>
</section>

<section>
  <div class="testimonials abs" role="img" aria-label="Smiling healthcare professionals in a pharmacy, tinted blue"></div>
  <h2 class="section-title testi-title abs">TESTIMONIALS</h2>
  <div class="round-arrow abs" style="left:25px"></div>
  <svg class="abs" style="left:40px;top:2718px" width="18" height="24"><path d="M14 2 L4 12 L14 22" fill="none" stroke="#fff" stroke-width="3"/></svg>
  <div class="round-arrow abs" style="left:1125px"></div>
  <svg class="abs" style="left:1142px;top:2718px" width="18" height="24"><path d="M4 2 L14 12 L4 22" fill="none" stroke="#fff" stroke-width="3"/></svg>

  <article class="testi-card abs" style="left:100px"><p>Nam libero tempore, cum soluta nobis<br>est eligendi optio cumque nihil impedit quo<br>minus id quod maxime placea</p><h4>Nora Whitfield</h4></article>
  <article class="testi-card abs" style="left:447px"><p>Nam libero tempore, cum soluta nobis<br>est eligendi optio cumque nihil impedit quo<br>minus id quod maxime placea</p><h4>Dana Calloway</h4></article>
  <article class="testi-card abs" style="left:795px"><p>Nam libero tempore, cum soluta nobis<br>est eligendi optio cumque nihil impedit quo<br>minus id quod maxime placea</p><h4>Owen Marsh</h4></article>
  <div class="avatar abs" style="left:210px" role="img" aria-label="Client portrait"></div>
  <div class="avatar abs" style="left:558px" role="img" aria-label="Client portrait"></div>
  <div class="avatar abs" style="left:906px" role="img" aria-label="Client portrait"></div>
</section>

<footer>
  <div class="site-footer abs"></div>
  <h3 class="foot-head abs" style="left:91px">ABOUT US</h3>
  <p class="foot-text abs" style="left:91px;top:3036px;width:265px">More importantly, we’re able to design strategies and solutions that improve this performance while also preserving your organization’s mission, vision, and strategic initiatives.</p>
  <span class="foot-social abs" style="left:91px"></span>
  <span class="foot-social abs" style="left:133px"></span>
  <span class="foot-social abs" style="left:175px"></span>
  <span class="foot-social abs" style="left:217px"></span>

  <h3 class="foot-head abs" style="left:387px">INFORMATION</h3>
  <ul class="foot-list abs" style="left:389px;top:3036px"><li>Home</li><li>About us</li><li>Services</li><li>Our Team</li><li>Contact</li></ul>

  <h3 class="foot-head abs" style="left:580px">CONTACT US</h3>
  <svg class="abs" style="left:580px;top:3042px" width="14" height="14" viewBox="0 0 24 24"><path d="M6 2 L10 7 L8 10 Q11 15 14 16 L17 14 L22 18 L19 22 Q8 21 2 6 Z" fill="#fff"/></svg>
  <span class="foot-text abs" style="left:602px;top:3037px">(555) 014-2290</span>
  <svg class="abs" style="left:580px;top:3078px" width="14" height="12" viewBox="0 0 24 18"><rect x="0" y="0" width="24" height="18" fill="#fff"/><path d="M0 0 L12 10 L24 0" fill="none" stroke="#2e2e2e" stroke-width="2"/></svg>
  <span class="foot-text abs" style="left:602px;top:3072px">info@quarrylinehealth.com</span>
  <svg class="abs" style="left:580px;top:3116px" width="12" height="16" viewBox="0 0 12 16"><path d="M6 16 Q0 8 0 6 A6 6 0 0 1 12 6 Q12 8 6 16 Z" fill="#fff"/><circle cx="6" cy="6" r="2" fill="#2e2e2e"/></svg>
  <p class="foot-text abs" style="left:602px;top:3110px">118 Harbor Street Suite 310<br>Fairview, NY 10099</p>

  <h3 class="foot-head abs" style="left:824px">EMAIL SUBSCRIPTION</h3>
  <p class="foot-text abs" style="left:824px;top:3037px">Register your email address to get information</p>
  <div class="sub-input abs">Email Address</div>
  <div class="sub-btn abs">Subscribe</div>

  <div class="foot-rule abs"></div>
  <p class="copyright abs">Copyrights © 2018. All Rights Reserved.</p>
</footer>

</body>
</html>
```